All Natural Mosquito Repellent

My company, BrightPebble Company has created an all natural mosquito repellent. I already have other all natural products that I have developed and created labels for. I will include a copy of that label so you have something to work from. I will need two labels. One for the front of the bottle and one for the back. The back label will need space for a UPC. The labels need to be 63mm (H) x 39mm (W)

Target Market(s)

Consumers, Organic, People who like natural products

Font styles to use
Other font styles liked:
• A combination of both Serif and Sans Serif

Requirements
Must have
• Use the words Organic, All Natural, Travel size, made in the USA label
Nice to have
• tag line: Don't beat them off. Spray them away.

```html
<!DOCTYPE html>
<html lang="en">
<head>
<meta charset="utf-8">
<title>BrightPebble Company – Mosquito Repellent Front Label</title>
<link href="https://fonts.googleapis.com/css2?family=Oswald:wght@500;600&family=Roboto+Condensed:ital,wght@0,700;1,400&family=Montserrat:wght@400;500&display=swap" rel="stylesheet">
<style>
  :root {
    --page-bg: #e4e4e4;
    --label-border: #123d1e;
    --sun-core: #f8d21a;
    --sun-mid: #f6a81c;
    --sun-edge: #ee8a1a;
    --forest-deep: #00301c;
    --forest-low: #0d4a22;
    --tree-green: #1f5a1e;
    --banner-rust: #b9552c;
    --brand-brown: #6b4a38;
    --mark-brown: #4b3a30;
    --ink-white: #ffffff;
    --stamp-rust: #b34a22;
  }
  * { margin: 0; padding: 0; box-sizing: border-box; }
  html, body { width: 1200px; height: 1200px; overflow: hidden; }
  body { background: var(--page-bg); position: relative; }

  .label {
    position: absolute;
    left: 290px; top: 100px;
    width: 620px; height: 1000px;
    border: 5px solid var(--label-border);
    border-radius: 16px;
    overflow: hidden;
    background: linear-gradient(180deg, var(--forest-deep) 0%, var(--forest-deep) 70%, var(--forest-low) 100%);
  }
  .sky {
    position: absolute; left: 0; top: 0; width: 100%; height: 330px;
    background: radial-gradient(ellipse 60% 70% at 50% 75%, var(--sun-core) 0%, var(--sun-mid) 45%, var(--sun-edge) 100%);
  }
  .brand-mark {
    position: absolute; left: 50%; top: 45px;
    width: 170px; height: 170px; margin-left: -85px;
    border-radius: 50%;
    background: var(--mark-brown);
  }
  .brand-name {
    position: absolute; left: 0; right: 0; top: 225px;
    text-align: center;
    font-family: "Montserrat", sans-serif; font-weight: 500;
    font-size: 27px; letter-spacing: 0.5px;
    color: var(--brand-brown);
  }
  .brand-note {
    position: absolute; left: 0; right: 0; top: 262px;
    text-align: center;
    font-family: "Montserrat", sans-serif; font-weight: 500;
    font-size: 11px; color: var(--brand-brown);
  }
  .treeline {
    position: absolute; left: 0; top: 280px; width: 100%; height: 82px;
    background: linear-gradient(180deg, rgba(31,90,30,0.0) 0%, var(--tree-green) 45%, var(--forest-deep) 100%);
  }
  .product-banner {
    position: absolute; left: 72px; top: 375px; width: 461px; height: 66px;
    background: var(--banner-rust);
    border: 2px solid #d98a5e;
    display: flex; align-items: center; justify-content: center;
    font-family: "Oswald", sans-serif; font-weight: 600;
    font-size: 44px; color: var(--ink-white); letter-spacing: 0.3px;
  }
  .claims {
    position: absolute; left: 0; right: 0; top: 452px;
    display: flex; justify-content: center; align-items: center; gap: 14px;
    font-family: "Roboto Condensed", sans-serif; font-weight: 700;
    font-size: 20px; color: var(--ink-white);
  }
  .claims .dot { width: 10px; height: 10px; border-radius: 50%; background: var(--ink-white); }
  .tagline-arcs { position: absolute; left: 0; top: 0; }
  .tagline {
    position: absolute; left: 0; right: 0; top: 583px;
    text-align: center;
    font-family: "Roboto Condensed", sans-serif; font-style: italic; font-weight: 400;
    font-size: 36px; line-height: 46px; color: var(--ink-white);
  }
  .shield { position: absolute; left: 278px; top: 757px; }
  .volume {
    position: absolute; left: 505px; top: 795px;
    font-family: "Roboto Condensed", sans-serif; font-weight: 700;
    font-size: 19px; color: var(--ink-white);
  }
  .protection-stamp {
    position: absolute; left: 62px; top: 838px;
    transform: rotate(-14deg);
    font-family: "Roboto Condensed", sans-serif; font-weight: 700;
    font-size: 22px; line-height: 20px; text-align: center;
    color: var(--stamp-rust);
    background: var(--ink-white);
    padding: 3px 8px; border-radius: 6px;
  }
  .made-in {
    position: absolute; left: 0; right: 0; top: 937px;
    text-align: center;
    font-family: "Montserrat", sans-serif; font-weight: 400;
    font-size: 26px; color: var(--ink-white);
  }
</style>
</head>
<body>
  <main class="label">
    <div class="sky"></div>
    <div class="brand-mark"></div>
    <div class="brand-name">BrightPebble Company</div>
    <div class="brand-note">crafted by hand, with love in the U.S.A.</div>
    <div class="treeline" role="img" aria-label="Silhouette of a pine forest treeline"></div>

    <div class="product-banner">MOSQUITO REPELLENT</div>
    <div class="claims">
      <span>ALL NATURAL</span><span class="dot"></span>
      <span>ORGANIC</span><span class="dot"></span>
      <span>TRAVEL SIZE</span>
    </div>

    <svg class="tagline-arcs" width="610" height="990" viewBox="0 0 610 990" aria-hidden="true">
      <path d="M235 560 Q 285 532 345 535 Q 290 540 235 560 Z" fill="#ffffff"/>
      <path d="M235 712 Q 290 734 345 718 Q 295 742 235 712 Z" fill="#ffffff"/>
      <path d="M0 908 Q 300 858 610 908" fill="none" stroke="#d8dccf" stroke-width="2"/>
    </svg>

    <div class="tagline">“Don’t beat them off<br>Spray them away”</div>

    <svg class="shield" width="104" height="120" viewBox="0 0 104 120" role="img" aria-label="Shield emblem with a mosquito">
      <path d="M52 4 L98 16 Q 98 80 52 116 Q 6 80 6 16 Z" fill="#ffffff" stroke="#9aa39c" stroke-width="4"/>
    </svg>
    <div class="volume">50 ML</div>

    <div class="protection-stamp">12 HOUR<br>PROTECTION</div>

    <div class="made-in">Made in the USA</div>
  </main>
</body>
</html>
```